NCBG website design

We need a page template website design for a cms website. Please see the brief attached for the details.
The client is the National Copperfleece Breeders Guild which is an organisation promoting the Copperfleece Sheep Breed within Australia.
Updates

Project Deadline Extended
Reason: So that my top few designs can make changes and re-submit.

Target Market(s)

See attached brief

```html
<!DOCTYPE html>
<html lang="en">
<head>
<meta charset="utf-8">
<title>National Copperfleece Breeders Guild</title>
<link href="https://fonts.googleapis.com/css2?family=Open+Sans:wght@400;600&display=swap" rel="stylesheet">
<style>
:root{
  --green:#0f9a47;
  --green-dark:#0a7e37;
  --green-light:#5aad3c;
  --yellow:#fdc93a;
  --orange:#fca21c;
  --text:#333;
  --muted:#666;
  --line:#ddd;
  --white:#fff;
}
*{box-sizing:border-box;margin:0;padding:0}
html,body{width:1042px;height:1200px;overflow:hidden;background:var(--white)}
body{position:relative;font-family:"Open Sans",sans-serif;color:var(--text)}
.abs{position:absolute}
.brand-mark{left:61px;top:22px;display:flex;align-items:center;gap:10px}
.brand-mark .dot{width:40px;height:40px;border-radius:50%;background:var(--green)}
.brand-mark span{font-size:30px;font-weight:600;color:var(--green)}
.site-title{left:271px;top:46px;font-size:22px;line-height:27px;color:#222}
.site-title .accent{color:var(--green)}
.search{left:736px;top:80px;width:237px;height:29px;border:1px solid var(--line);font-size:11px;font-style:italic;color:#999;padding:7px 12px}
.search svg{position:absolute;right:10px;top:6px}
.main-nav{left:61px;top:118px;width:919px;height:48px;background:linear-gradient(#fdd54a,#fdb42a);border-radius:3px 3px 0 0;display:flex;list-style:none}
.main-nav li{font-size:15px;line-height:48px;padding:0 17px;color:#222;white-space:nowrap}
.main-nav li.active{background:linear-gradient(#1aa456,#0b8a3d);color:var(--white);padding:0 25px}
.dropdown{left:148px;top:164px;width:149px;height:73px;background:linear-gradient(#1aa456,#0b8a3d);padding:12px 0 0 25px;color:var(--white);font-size:12px;line-height:25px;white-space:nowrap;box-shadow:0 2px 3px rgba(0,0,0,.25)}
.hero{left:61px;top:166px;width:919px;height:343px;background:linear-gradient(#cfe0f2 0%,#a9c1dc 20%,#6d8a5a 38%,#4d6d3a 60%,#5e9e3e 80%,#4d8a32 100%);border:1px solid var(--orange)}
.hero-dots{left:501px;top:487px;display:flex;gap:4px}
.hero-dots i{width:10px;height:10px;border-radius:50%;background:#e8e8e8;display:block}
h1{position:absolute;left:63px;top:536px;font-size:27px;font-weight:400;color:#333}
.intro{left:65px;top:574px;width:650px;font-size:12px;line-height:20px;color:#555}
.aims-title{left:65px;top:645px;font-size:13.5px;color:#333}
.aims{left:68px;top:681px;list-style:none;font-size:12px;color:#555}
.aims li{height:24px;display:flex;align-items:center;gap:8px}
h2{position:absolute;font-size:20px;font-weight:400}
.news-heading{left:64px;top:794px;color:var(--green)}
.do-heading{left:393px;top:794px;color:var(--orange)}
.news-list{left:64px;top:834px;width:300px}
.news-item{margin-bottom:13px}
.news-item h3{font-size:13.5px;font-weight:400;color:#333;margin-bottom:4px}
.news-item p{font-size:11.5px;line-height:20px;color:#666}
.news-item time{display:block;font-size:11.5px;color:var(--green);margin-top:5px}
.what-photo{left:395px;top:832px;width:289px;height:110px;background:linear-gradient(#6b7b88,#9a8a62 55%,#c9b48a)}
.what-text{left:395px;top:951px;width:290px;font-size:11.5px;line-height:20px;color:#666;text-align:justify}
.btn{left:395px;top:1020px;width:104px;height:29px;background:linear-gradient(#fdb53a,#fc8f12);border-radius:3px;color:var(--white);font-size:12px;line-height:29px;text-align:center}
.tile{position:absolute;left:744px;width:236px;border:3px solid #f1f1f1;color:var(--white);font-size:17px;line-height:20px;padding:0 22px;display:flex;align-items:center;justify-content:space-between}
.tile.yellow{background:linear-gradient(#fdca3a,#fca21c)}
.tile.green{background:linear-gradient(#1aa456,#0b8a3d)}
.tile.lime{background:linear-gradient(#6ab84a,#4a9e32)}
.tile-helpline{top:536px;height:67px}
.tile-events{top:612px;height:65px}
.tile-members{top:687px;height:81px;flex-direction:column;padding:0;align-items:stretch}
.tile-members div{display:flex;align-items:center;justify-content:space-between;padding:0 16px 0 22px;flex:1;white-space:nowrap;font-size:15.5px}
.tile-members div+div{border-top:1px solid rgba(255,255,255,.45);font-size:14px}
.tile-news{top:777px;height:69px}
.sponsors{left:744px;top:858px;width:236px;height:174px;border:1px solid var(--line)}
.sponsor-name{position:absolute;left:30px;top:46px;display:flex;align-items:center;gap:8px}
.sponsor-name .dot{width:30px;height:30px;background:#f2d22a;border-radius:50%}
.sponsor-name span{font-size:22px;font-weight:600;color:var(--green-dark)}
.sponsors-bar{position:absolute;left:0;bottom:0;width:100%;height:42px;border-top:1px solid var(--line);background:#f7f7f7;font-size:15px;line-height:42px;padding-left:18px;color:#222}
.sponsors-bar svg{position:absolute;right:14px;top:14px}
.footer{left:0;top:1093px;width:1042px;height:107px;border-top:1px solid var(--line);background:linear-gradient(#fff,#f4f4f4)}
.copyright{position:absolute;left:65px;top:26px;font-size:12.5px;line-height:25px;color:#333}
.social{position:absolute;left:850px;top:25px;display:flex;align-items:center;gap:10px;font-size:12.5px;color:#333}
.social i{display:block;width:28px;height:28px;background:#3b5998;border-radius:3px}
</style>
</head>
<body>
<header>
  <div class="abs brand-mark"><div class="dot"></div><span>NCBG</span></div>
  <div class="abs site-title">National Copperfleece<br><span class="accent">Breeders Guild</span></div>
  <div class="abs search">Search here..
    <svg width="16" height="16" viewBox="0 0 16 16"><circle cx="6.5" cy="6.5" r="5" fill="none" stroke="#999" stroke-width="2"/><line x1="10" y1="10" x2="14.5" y2="14.5" stroke="#999" stroke-width="2.5"/></svg>
  </div>
  <ul class="abs main-nav">
    <li style="padding-left:27px">HOME</li><li class="active">ABOUT</li><li>SEARCH</li><li>MEMBER SERVICES</li><li>STUD PAGES</li><li style="padding:0 19px">NEWS</li><li style="padding:0 19px">SALES</li><li style="padding:0 19px">LINKS</li><li style="padding:0 19px">CONTACT</li>
  </ul>
</header>
<div class="abs hero" role="img" aria-label="Flock of Copperfleece sheep grazing in a green paddock below forested hills"></div>
<div class="abs hero-dots"><i></i><i></i><i></i></div>
<div class="abs dropdown">BREED<br>GENETIC TESTING</div>

<main>
  <h1>Welcome to Our Website Mainpage</h1>
  <p class="abs intro">The Copperfleece is an Australian breed developed for Australian conditions. The Copperfleece is proving to be the ideal prime lamb terminal sire in wide-ranging areas and environments of Australia. It is giving outstanding results in the dry, arid, pastoral zones; all types of agricultural, mixed farming areas; and also in higher rainfall districts.</p>
  <p class="abs aims-title">The NATIONAL COPPERFLEECE BREEDERS GUILD aims to:</p>
  <ul class="abs aims">
    <li><svg width="16" height="12" viewBox="0 0 16 12"><path d="M1 6l4 4 10-9" fill="none" stroke="#0f9a47" stroke-width="3"/></svg>be at the forefront of marketing and promotion of the Copperfleece breed</li>
    <li><svg width="16" height="12" viewBox="0 0 16 12"><path d="M1 6l4 4 10-9" fill="none" stroke="#0f9a47" stroke-width="3"/></svg>better educate our members and commerical breeders on providing superior genetics to the Australian lamb</li>
    <li><svg width="16" height="12" viewBox="0 0 16 12"><path d="M1 6l4 4 10-9" fill="none" stroke="#0f9a47" stroke-width="3"/></svg>continue to develop the Copperfleece breed to the advantage of all involved in the Australian lamb industry</li>
  </ul>

  <h2 class="news-heading">Latest News &amp; Blog</h2>
  <div class="abs news-list">
    <article class="news-item"><h3>Etiam eu urna Sed</h3><p>Malesuada nec ultricies sit amet porttitor mattis enim<br>In massa libero interdum nec</p><time>25 April 2014</time></article>
    <article class="news-item"><h3>Mauris nunc quam venenatis nec</h3><p>Etiam est nunc venenatis in tristique eu imperdiet<br>ac nisl Cum sociis natoque penatibus et magnis dis<br>parturient montes nascetur</p><time>18 April 2014</time></article>
  </div>

  <h2 class="do-heading">What We Do</h2>
  <div class="abs what-photo" role="img" aria-label="Group of Copperfleece rams standing in a line"></div>
  <p class="abs what-text">Donec dictum lectus non odio Cras a ante vitae enim iaculis aliquam Mauris nunc quam venenatis nec euismod sit amet egestas placerat est</p>
  <div class="abs btn">READ MORE</div>
</main>

<aside>
  <div class="tile yellow tile-helpline">PRIME LAMB<br>HELPLINE
    <svg width="36" height="36" viewBox="0 0 36 36"><path d="M8 3l6 7-3 4c2 5 6 9 11 11l4-3 7 6-4 5C18 32 4 18 3 7z" fill="none" stroke="#fff" stroke-width="2.5" stroke-linejoin="round"/></svg></div>
  <div class="tile green tile-events">EVENTS
    <svg width="44" height="42" viewBox="0 0 44 42"><rect x="2" y="6" width="40" height="34" rx="3" fill="none" stroke="#fff" stroke-width="2.5"/><line x1="2" y1="14" x2="42" y2="14" stroke="#fff" stroke-width="2"/><g fill="#fff"><rect x="10" y="1" width="3" height="8"/><rect x="20" y="1" width="3" height="8"/><rect x="31" y="1" width="3" height="8"/><rect x="10" y="19" width="5" height="4"/><rect x="19" y="19" width="5" height="4"/><rect x="28" y="19" width="5" height="4"/><rect x="10" y="27" width="5" height="4"/><rect x="19" y="27" width="5" height="4"/><rect x="28" y="27" width="5" height="4"/></g></svg></div>
  <div class="tile yellow tile-members">
    <div>MEMBERS RESOURCE<svg width="22" height="24" viewBox="0 0 24 26"><circle cx="12" cy="7" r="6" fill="#fff"/><path d="M0 26c0-9 5-12 12-12s12 3 12 12z" fill="#fff"/></svg></div>
    <div>WEBMANAGER LOGIN<svg width="26" height="26" viewBox="0 0 28 28"><circle cx="8" cy="20" r="6" fill="none" stroke="#fff" stroke-width="3"/><path d="M12 16L25 3M20 8l3 3M23 5l3 3" stroke="#fff" stroke-width="3"/></svg></div>
  </div>
  <div class="tile lime tile-news">LATEST NEWS
    <svg width="50" height="50" viewBox="0 0 50 50"><path d="M6 40l22-26 8 20z" fill="#fff"/><path d="M10 36l6 10 5-4-4-8" fill="#fff"/><path d="M36 8a10 10 0 0 1 4 12M40 3a16 16 0 0 1 6 18" fill="none" stroke="#fff" stroke-width="2.5"/></svg></div>
  <div class="abs sponsors">
    <div class="sponsor-name"><div class="dot"></div><span>Copperfleece</span></div>
    <div class="sponsors-bar">SPONSORS MEMERSHIP
      <svg width="22" height="14" viewBox="0 0 22 14"><path d="M7 1L1 7l6 6M15 1l6 6-6 6" fill="none" stroke="#999" stroke-width="1.5"/></svg></div>
  </div>
</aside>

<footer class="abs footer">
  <p class="copyright">Copyright National Copperfleece Breeders Guild<br>Website design and development by Fernwick Studio</p>
  <div class="social">Stay in touch <i></i></div>
</footer>
</body>
</html>
```